Harcourt Power Gym Chronic Pain Flyer

Double sided DL flyer required to promote a strength training studio to sufferers of chronic pain. Flyer will be displayed in osteopathy, chiropractic and massage clinics. Flyer should be clean, professional and appeal to an older (40+) demographic.

Target Market(s)

Chronic pain sufferers. Age 40+

Industry/Entity Type

Health And Wellness

Colors

Designer to choose colors to be used in the design.

Requirements
Must have
• See attached files for text copy and logo. Image(s) of people strength training with a coach or personal trainer, as well as images depicting pain in common parts of the body (such as those pictured in the supplied mock up)
• website address: harcourtpowergym.com.au
• phone number : 0458 214 963
• Street address: 3/14 Birchwood Rd, Harcourt
Nice to have
• Images such as in the attached files.

```html
<!DOCTYPE html>
<html lang="en">
<head>
<meta charset="utf-8">
<title>Harcourt Power Gym – Chronic Pain DL Flyer</title>
<link href="https://fonts.googleapis.com/css2?family=Poppins:wght@300;400;500;600;700;800;900&display=swap" rel="stylesheet">
<style>
  :root {
    --bg: #f2f2f2;
    --charcoal: #2b2b2b;
    --charcoal-deep: #1e1e1e;
    --red: #d32027;
    --red-bright: #ee3b35;
    --white: #ffffff;
    --ink: #1c1c1c;
  }
  * { box-sizing: border-box; margin: 0; padding: 0; }
  html, body { width: 1200px; height: 1200px; overflow: hidden; }
  body { background: var(--bg); font-family: "Poppins", sans-serif; position: relative; }

  .flyer { position: absolute; width: 349px; height: 739px; overflow: hidden; }
  .flyer--front { left: 229px; top: 239px; background: linear-gradient(180deg, var(--charcoal-deep) 0%, var(--charcoal) 60%, var(--charcoal-deep) 100%); }
  .flyer--back { left: 635px; top: 239px; background: linear-gradient(180deg, #ffffff 30%, #f4f4f4 70%, #d6d6d6 100%); }
  .flyer svg.shapes { position: absolute; inset: 0; width: 100%; height: 100%; }

  .photo { position: absolute; }
  .photo--back-pain {
    left: 0; top: 0; width: 349px; height: 420px;
    background:
      radial-gradient(ellipse 80px 50px at 175px 262px, rgba(226,38,38,.9), rgba(226,38,38,0) 100%),
      linear-gradient(90deg, rgba(30,30,30,.85) 0%, rgba(30,30,30,0) 22%, rgba(30,30,30,0) 78%, rgba(30,30,30,.85) 100%),
      linear-gradient(180deg, #5e5e5e 0%, #9c9c9c 25%, #a8a8a8 50%, #7a7a7a 75%, #2b2b2b 100%);
  }
  .photo--knee-pain {
    right: 0; top: 190px; width: 200px; height: 260px;
    background:
      radial-gradient(ellipse 55px 70px at 120px 130px, rgba(232,60,60,.85), rgba(232,60,60,0) 100%),
      linear-gradient(90deg, rgba(255,255,255,0) 0%, #d9d9d9 40%, #c2c2c2 100%);
    -webkit-mask-image: linear-gradient(180deg, transparent 0%, #000 12%, #000 80%, transparent 100%);
    mask-image: linear-gradient(180deg, transparent 0%, #000 12%, #000 80%, transparent 100%);
  }
  .photo--shoulder-pain {
    left: 0; top: 360px; width: 145px; height: 260px;
    background:
      radial-gradient(ellipse 40px 40px at 50px 70px, rgba(232,80,80,.8), rgba(232,80,80,0) 100%),
      linear-gradient(90deg, #bdbdbd 0%, #d2d2d2 60%, rgba(255,255,255,0) 100%);
    -webkit-mask-image: linear-gradient(180deg, transparent 0%, #000 12%, #000 78%, transparent 100%);
    mask-image: linear-gradient(180deg, transparent 0%, #000 12%, #000 78%, transparent 100%);
  }

  .brand-name {
    position: absolute; left: 0; right: 0; top: 343px; text-align: center;
    color: var(--white); font-weight: 700; font-size: 24px; letter-spacing: .5px;
  }

  .headline {
    position: absolute; left: 0; right: 0; text-align: center;
    font-weight: 900; text-transform: uppercase; color: var(--white);
    font-size: 43px; line-height: 33px; letter-spacing: -.5px;
  }
  .flyer--front .headline { top: 440px; }
  .flyer--back .headline { top: 26px; }

  .tagline {
    position: absolute; left: 34px; width: 280px; top: 126px; height: 22px;
    border: 1.5px solid var(--red); color: var(--red);
    font-size: 15.5px; font-weight: 500; text-align: center; line-height: 19px; text-transform: uppercase;
  }

  .copy { position: absolute; font-size: 12.3px; line-height: 15px; color: var(--ink); }
  .copy--intro { left: 23px; top: 248px; width: 175px; }
  .copy--studio { left: 151px; top: 402px; width: 190px; }
  .copy--helped { left: 151px; top: 462px; width: 190px; }
  .cta { position: absolute; left: 151px; top: 514px; width: 190px; color: var(--red); font-weight: 700; font-size: 14px; line-height: 18px; text-transform: uppercase; }

  .contact { position: absolute; left: 0; right: 0; text-align: center; }
  .flyer--front .contact { top: 626px; color: var(--white); }
  .flyer--back .contact { top: 622px; color: var(--ink); }
  .contact__phone { font-size: 26px; font-weight: 700; line-height: 30px; display: flex; justify-content: center; align-items: center; gap: 6px; }
  .contact__address { font-size: 17px; font-weight: 400; line-height: 19px; margin-top: 3px; display: flex; justify-content: center; gap: 6px; }
  .contact__address svg, .contact__phone svg { flex: none; }
  .contact__address svg { margin-top: 2px; }

  .web-band {
    position: absolute; left: 0; right: 0; bottom: 0; height: 31px;
    background: linear-gradient(90deg, #b71c20, var(--red) 50%, #b71c20);
    color: var(--white); text-align: center; font-size: 17px; line-height: 31px;
  }
  .web-band b { font-weight: 700; }
  .web-band span { font-weight: 300; }
</style>
</head>
<body>

<section class="flyer flyer--front">
  <div class="photo photo--back-pain" role="img" aria-label="Black and white photo of a man's bare back with hands on his lower back, red glow showing pain"></div>
  <svg class="shapes" viewBox="0 0 349 739" aria-hidden="true">
    <path d="M52 580 Q200 548 349 595 L349 625 Q230 572 52 580 Z" fill="#e3322f"/>
  </svg>
  <div class="brand-name">HARCOURT POWER GYM</div>
  <h1 class="headline">Health<br>Through<br>Strength</h1>
  <div class="contact">
    <div class="contact__phone">
      <svg width="20" height="20" viewBox="0 0 24 24"><path fill="#e3322f" d="M6.6 10.8a15.1 15.1 0 0 0 6.6 6.6l2.2-2.2c.3-.3.7-.4 1-.2 1.1.4 2.3.6 3.6.6.6 0 1 .4 1 1V20c0 .6-.4 1-1 1A17 17 0 0 1 3 4c0-.6.4-1 1-1h3.5c.6 0 1 .4 1 1 0 1.3.2 2.5.6 3.6.1.3 0 .7-.2 1z"/></svg>
      0458 214 963
    </div>
    <div class="contact__address">
      <svg width="16" height="20" viewBox="0 0 16 20"><path fill="none" stroke="#e3322f" stroke-width="2.4" d="M8 18.5S2 11.8 2 7.5a6 6 0 0 1 12 0c0 4.3-6 11-6 11z"/><circle cx="8" cy="7.5" r="2" fill="#e3322f"/></svg>
      <span>3/14 Birchwood Rd,<br>Harcourt, VIC, 3453</span>
    </div>
  </div>
  <div class="web-band"><b>harcourtpowergym</b><span>.com.au</span></div>
</section>

<section class="flyer flyer--back">
  <div class="photo photo--knee-pain" role="img" aria-label="Black and white photo of hands holding a knee, red glow showing pain"></div>
  <div class="photo photo--shoulder-pain" role="img" aria-label="Black and white photo of a hand on a shoulder, red glow showing pain"></div>
  <svg class="shapes" viewBox="0 0 349 739" aria-hidden="true">
    <path d="M0 0 H349 V150 Q250 205 150 203 Q55 200 0 145 Z" fill="#2b2b2b"/>
    <path d="M25 158 Q150 225 349 150 V168 Q170 240 25 158 Z" fill="#d32027"/>
    <path d="M50 592 Q220 564 349 602 V632 Q230 580 50 592 Z" fill="#d32027"/>
  </svg>
  <h2 class="headline">Health<br>Through<br>Strength</h2>
  <div class="tagline">You don't have to live in pain</div>
  <p class="copy copy--intro">Strength training has been shown to improve many chronic pain conditions and is now routinely recommended by medical and health professionals.</p>
  <p class="copy copy--studio">Our private studio provides high quality strength training by expert strength coaches.</p>
  <p class="copy copy--helped">We've helped countless people improve or eliminate chronic pain.</p>
  <p class="cta">Contact us today<br>and find out how<br>we can help you.</p>
  <div class="contact">
    <div class="contact__phone">
      <svg width="20" height="20" viewBox="0 0 24 24"><path fill="#d32027" d="M6.6 10.8a15.1 15.1 0 0 0 6.6 6.6l2.2-2.2c.3-.3.7-.4 1-.2 1.1.4 2.3.6 3.6.6.6 0 1 .4 1 1V20c0 .6-.4 1-1 1A17 17 0 0 1 3 4c0-.6.4-1 1-1h3.5c.6 0 1 .4 1 1 0 1.3.2 2.5.6 3.6.1.3 0 .7-.2 1z"/></svg>
      0458 214 963
    </div>
    <div class="contact__address">
      <svg width="16" height="20" viewBox="0 0 16 20"><path fill="none" stroke="#d32027" stroke-width="2.4" d="M8 18.5S2 11.8 2 7.5a6 6 0 0 1 12 0c0 4.3-6 11-6 11z"/><circle cx="8" cy="7.5" r="2" fill="#d32027"/></svg>
      <span>3/14 Birchwood Rd,<br>Harcourt, VIC, 3453</span>
    </div>
  </div>
  <div class="web-band"><b>harcourtpowergym</b><span>.com.au</span></div>
</section>

</body>
</html>
```